Up and coming writing company needs a wordpress site. Our company is called PLUM INKWORKS

We need to get a wordpress site up so that we can continue to grow our business. We already have a growing list of clients, but we want to expand beyond our existing contact list. We want our site to have a vintage feel (old typewriters, antiques, etc.). We want it to feel unique and quirky.

We love this website's look and feel: http://brindlequay.example/

Industry/Entity Type

Business

Colors
d0ebe7
e9f1ce
fee4d5

Requirements
Must have
• a button that says US
a button that says YOU
a button that says THEM
All three of those buttons need to have space underneath them for additional text. They are going to be the click options in the website
The website should say PLUM INKWORKS at the top with the logo
Underneath it should say "We help you say what you want to say the way you want to say it."
Nice to have
• A cool antique picture (typewriter, sewing machine, etc), perhaps as a backdrop
Should not have
• Busyness.

```html
<!DOCTYPE html>
<html lang="en">
<head>
<meta charset="utf-8">
<title>Plum Inkworks</title>
<link rel="stylesheet" href="https://fonts.googleapis.com/css2?family=Open+Sans:wght@300;400;600&family=Arimo:wght@400&display=swap">
<style>
:root{
  --ink:#4a4a4a;
  --nav:#4d4d4d;
  --mint:#a9d3c4;
  --teal:#2e8b6f;
  --teal-dark:#237058;
  --grey:#8a8a8a;
  --line:#e2e2e2;
  --footer:#333333;
  --footer-text:#e8e8e8;
}
*{box-sizing:border-box;margin:0;padding:0}
html,body{width:1030px;height:1200px;overflow:hidden;background:#fff}
body{position:relative;font-family:"Open Sans",Arial,sans-serif;color:var(--ink)}
.brand{position:absolute;left:80px;top:14px;display:flex;align-items:center;gap:10px}
.brand-dot{width:40px;height:40px;border-radius:50%;background:var(--mint)}
.brand-name{font-weight:600;font-size:24px;letter-spacing:3px;color:var(--nav)}
.social{position:absolute;right:86px;top:22px;display:flex;gap:14px}
.social span{width:28px;height:28px;border:1px solid #ddd;background:#f5f5f5;display:block}
.call{position:absolute;right:86px;top:60px;font-family:Arimo,sans-serif;font-size:16px;color:#777}
.nav{position:absolute;left:56px;top:94px;width:918px;height:54px;background:var(--nav);display:flex;box-shadow:0 10px 12px -8px rgba(0,0,0,.4)}
.nav-home,.nav-search{width:55px;background:var(--mint);display:flex;align-items:center;justify-content:center}
.nav-search{margin-left:auto}
.nav-items{display:flex;align-items:center;list-style:none;padding-left:22px}
.nav-items li{color:#fff;font-size:13.5px;margin-right:44px;display:flex;align-items:center;gap:8px}
.caret{border:5px solid transparent;border-top-color:#aaa;margin-top:5px}
.band{position:absolute;left:0;top:162px;width:1030px;height:10px;background:#f7f7f7;border-top:1px solid #e6e6e6}
.hero{position:absolute;left:0;top:172px;width:1030px;height:435px;background:linear-gradient(90deg,#ececea,#f6f6f5)}
.hero-photo{position:absolute;left:0;top:0;width:590px;height:435px;background:radial-gradient(ellipse at 45% 55%,#b4bd9c 0%,#c9cfb6 45%,#ecedea 80%)}
.hero-copy{position:absolute;left:601px;top:136px;font-weight:300;font-size:34px;line-height:38px;letter-spacing:.6px;color:#666}
.register{position:absolute;left:611px;top:274px;width:145px;height:42px;background:var(--teal);border-bottom:2px solid var(--teal-dark);color:#fff;font-size:14px;letter-spacing:-.4px;display:flex;align-items:center;justify-content:center;gap:9px}
.register i{width:17px;height:17px;border-radius:50%;background:#1f5e4b;display:flex;align-items:center;justify-content:center}
.dots{position:absolute;left:869px;top:410px;display:flex;gap:8px}
.dots span{width:12px;height:12px;border-radius:50%;background:#aaa}
.dots span:first-child{background:#777}
.tiles{position:absolute;left:94px;top:615px;display:flex;gap:18px}
.tile{width:269px;height:174px;border:1px solid var(--line);box-shadow:inset 0 0 12px rgba(0,0,0,.06);display:flex;flex-direction:column;align-items:center;padding-top:22px}
.tile-icon{height:58px;display:flex;align-items:center}
.tile h2{font-family:Arimo,sans-serif;font-weight:400;font-size:22px;color:#666;margin-top:16px}
.tile p{font-family:Arimo,sans-serif;font-size:11px;letter-spacing:.3px;color:var(--grey);margin-top:8px}
.vision-art{position:absolute;left:92px;top:859px;width:219px;height:151px;border:1px solid #ddd;background:#fff;padding:8px}
.vision-art div{width:100%;height:100%;background:linear-gradient(#e8e2d2,#d9d2c0)}
.vision{position:absolute;left:332px;top:858px;width:580px}
.vision h3{font-weight:400;font-size:22px;color:var(--teal)}
.vision p{font-family:Arimo,sans-serif;font-size:10.5px;letter-spacing:.4px;color:#888;line-height:13px;margin-top:10px}
.shares{position:absolute;left:330px;top:983px;display:flex;gap:10px;font-family:Arimo,sans-serif;font-size:10px}
.share{display:flex;gap:4px}
.share b{font-weight:400;padding:2px 5px;border:1px solid #ccd;background:#eef0f6;color:#335}
.share em{font-style:normal;padding:2px 5px;border:1px solid #ccc;background:#fff;color:#555}
.share.orange b{background:#e8653f;border-color:#e8653f;color:#fff}
.footer{position:absolute;left:0;top:1047px;width:1030px;height:153px;background:var(--footer);font-family:Arimo,sans-serif;color:var(--footer-text)}
.footer-links{position:absolute;left:101px;top:18px;font-size:11px;letter-spacing:.4px;display:flex;gap:16px;list-style:none}
.address{position:absolute;right:79px;top:20px;text-align:right;font-style:normal;font-size:10.5px;line-height:13px;letter-spacing:.4px}
.copyright{position:absolute;left:0;width:100%;top:137px;text-align:center;font-size:10.5px;color:#777;letter-spacing:.4px}
</style>
</head>
<body>
<header>
  <div class="brand"><span class="brand-dot"></span><span class="brand-name">PLUM INKWORKS</span></div>
  <div class="social"><span></span><span></span><span></span></div>
  <div class="call">Call Us : +01 555-0142</div>
  <nav class="nav">
    <div class="nav-home"><svg width="18" height="16" viewBox="0 0 18 16"><path d="M9 0L0 8h2.5v8h4.5v-5h4v5h4.5V8H18z" fill="#fff"/></svg></div>
    <ul class="nav-items">
      <li>Services <span class="caret"></span></li>
      <li>About <span class="caret"></span></li>
      <li>News and Blog</li>
      <li>Working with Us</li>
      <li style="margin-right:56px">Client</li>
      <li>Contact</li>
    </ul>
    <div class="nav-search"><svg width="18" height="18" viewBox="0 0 18 18"><circle cx="7" cy="7" r="5.5" fill="none" stroke="#fff" stroke-width="2"/><path d="M11 11l6 6" stroke="#fff" stroke-width="2"/></svg></div>
  </nav>
</header>
<div class="band"></div>
<section class="hero">
  <div class="hero-photo" role="img" aria-label="Photograph of a vintage sage green portable typewriter"></div>
  <p class="hero-copy">We help you say<br>what you want to say<br>the way you want to say it</p>
  <a class="register">REGISTER NOW <i><svg width="7" height="9" viewBox="0 0 7 9"><path d="M1 1l4 3.5L1 8" stroke="#fff" stroke-width="2" fill="none"/></svg></i></a>
  <div class="dots"><span></span><span></span><span></span><span></span></div>
</section>
<section class="tiles">
  <a class="tile">
    <span class="tile-icon"><svg viewBox="0 0 84 66" width="74" height="58"><path d="M2 8l38 8v48L2 56zM44 16L74 0l10 44-40 20z" fill="#bbb"/></svg></span>
    <h2>US</h2>
    <p>Who we are and how we write</p>
  </a>
  <a class="tile">
    <span class="tile-icon"><svg viewBox="0 0 68 68" width="58" height="58"><rect x="1" y="1" width="66" height="66" fill="#ddd" stroke="#bbb"/><rect x="1" y="1" width="66" height="12" fill="#bbb"/><g fill="#bbb"><rect x="15" y="17" width="9" height="9"/><rect x="27" y="17" width="9" height="9"/><rect x="39" y="17" width="9" height="9"/><rect x="51" y="17" width="9" height="9"/><rect x="4" y="30" width="9" height="9"/><rect x="15" y="30" width="9" height="9"/><rect x="27" y="30" width="9" height="9"/><rect x="39" y="30" width="9" height="9"/><rect x="51" y="30" width="9" height="9"/><rect x="4" y="43" width="9" height="9"/><rect x="15" y="43" width="9" height="9"/><rect x="27" y="43" width="9" height="9"/><rect x="39" y="43" width="9" height="9"/><rect x="51" y="43" width="9" height="9"/><rect x="4" y="55" width="9" height="9"/><rect x="15" y="55" width="9" height="9"/><rect x="27" y="55" width="9" height="9"/></g></svg></span>
    <h2>YOU</h2>
    <p>What we can write for you</p>
  </a>
  <a class="tile">
    <span class="tile-icon"><svg viewBox="0 0 56 70" width="47" height="58"><path d="M12 32V22a16 16 0 0 1 32 0v10" fill="none" stroke="#bbb" stroke-width="8"/><rect x="2" y="30" width="52" height="40" rx="4" fill="#bbb"/></svg></span>
    <h2>THEM</h2>
    <p>The clients we write with</p>
  </a>
</section>
<div class="vision-art"><div role="img" aria-label="Illustration of a black vintage typewriter"></div></div>
<section class="vision">
  <h3>Our Vision</h3>
  <p>Our vision is to become the UK's Will Writing Company of choice, and we know that to achieve this we need to ensure that our strong internal values continue to be reflected in how we treat our customers.</p>
  <p style="margin-top:16px">Our mission is to provide peace of mind and add value to every interaction we have with you</p>
</section>
<div class="shares">
  <span class="share"><b>Like</b><em>3k</em></span>
  <span class="share"><b>Post</b><em>316</em></span>
  <span class="share"><b>+1</b><em>81</em></span>
  <span class="share orange"><b>Share</b><em>4.6K</em></span>
</div>
<footer class="footer">
  <ul class="footer-links">
    <li>Services</li><li>|</li><li>About |</li><li>News and Blog</li><li>|</li><li>Working with Us</li><li>Client</li><li>|</li><li>Contact Us</li>
  </ul>
  <address class="address">PLUM INKWORKS Company Ltd.<br>Quill House,<br>Ferrow Lane,<br>Ashcombe Trade Park,<br>Westmarsh WM4 2RT<br>Company No. 4827159<br>0120 555018822</address>
  <p class="copyright">© Copyright Plum Inkworks Company 2013. All Rights Reserved.&nbsp; Terms &amp; Conditions | Website Disclaimer | Privacy Policy</p>
</footer>
</body>
</html>
```